Pay-Per-Use Production Space Warehouse/Factory/Production Space

Please refer to project requirements as attached/included. This is an introductory marketing Info graphic to capture attention or create awareness to a new, epic and unique business value preposition and business model for customer to easily launch new products/services and robust supply chain. This is a win win revolutionary business solution compare with traditional or conventional methods of outsourcing or DIY design, build, finance, operate and maintain. PROJECT Requirement to info graphic designer
1) Subject to confidentiality and all rights reserved
2) Below are some photos which you may consider to use for this work
3) Clarify and verify with us if there are any questions related to this work and design

Target Market(s)

Global, (Life sciences, food, others)

Industry/Entity Type

Medical And Science

Requirements
Must have
• Dynamic background template.
Should not have
• Monotonous and un-creative designs

```html
<!DOCTYPE html>
<html lang="en">
<head>
<meta charset="utf-8">
<title>Pay-Per-Use Location</title>
<link href="https://fonts.googleapis.com/css2?family=Roboto+Condensed:wght@400;700;800&family=Open+Sans:wght@400;600;700&display=swap" rel="stylesheet">
<style>
  :root {
    --ink: #1d1d1f;
    --night: #0a0a0a;
    --accent: #d4472a;
    --accent-dark: #b63a20;
    --paper: #ffffff;
    --rule: #bdbdbd;
    --muted: #666666;
  }
  html, body { margin: 0; padding: 0; overflow: hidden; background: var(--paper); }
  .sheet {
    position: relative;
    width: 849px; height: 1200px;
    background: var(--paper);
    font-family: "Open Sans", Arial, sans-serif;
    color: var(--ink);
    overflow: hidden;
  }
  .hero-visual {
    position: absolute; left: 0; top: 0;
    width: 849px; height: 792px;
    background:
      radial-gradient(ellipse 460px 420px at 570px 400px, rgba(160,160,160,.55) 0%, rgba(90,90,90,.35) 45%, rgba(20,20,20,0) 75%),
      radial-gradient(ellipse 320px 220px at 360px 120px, rgba(140,140,140,.3), rgba(0,0,0,0) 70%),
      linear-gradient(180deg, #151515 0%, var(--night) 100%);
  }
  .offer-panel {
    position: absolute; left: 113px; top: 405px;
    width: 348px; height: 353px;
  }
  .offer-panel svg.panel-shape { position: absolute; left: 0; top: 0; }
  .offer-title {
    position: absolute; left: 0; top: 22px; width: 348px;
    margin: 0; text-align: center;
    font-family: "Roboto Condensed", Arial, sans-serif;
    font-weight: 800; font-size: 28px; line-height: 30px;
    color: var(--paper);
  }
  .offer-icons {
    position: absolute; left: 0; top: 110px; width: 348px;
    display: flex; justify-content: center; gap: 26px;
  }
  .offer-icons svg { width: 48px; height: 48px; }
  .offer-reach {
    position: absolute; left: 0; top: 186px; width: 348px;
    margin: 0; text-align: center;
    font-family: "Roboto Condensed", Arial, sans-serif;
    font-weight: 800; font-size: 28px; line-height: 25px;
    color: var(--paper);
  }
  .offer-note {
    position: absolute; left: 0; top: 264px; width: 348px;
    margin: 0; text-align: center;
    font-family: "Roboto Condensed", Arial, sans-serif;
    font-size: 16px; line-height: 18px; color: var(--paper);
  }
  .broker-note {
    position: absolute; left: 50px; top: 962px; width: 126px;
    padding: 8px 0;
    border-top: 2px solid var(--accent); border-bottom: 2px solid var(--accent);
    text-align: center; font-size: 11px; line-height: 14px; font-weight: 600;
    color: var(--ink);
  }
  .details {
    position: absolute; left: 283px; top: 856px; width: 490px;
    font-size: 15px; line-height: 20px;
  }
  .details p { margin: 0; }
  .details .strong { font-weight: 700; }
  .details .divider { border-top: 1px solid var(--rule); margin: 6px 0 8px; }
  .details .highlight { color: var(--accent); font-weight: 700; margin-top: 10px; }
  .footer { position: absolute; left: 0; top: 0; }
  .footer .contract { position: absolute; left: 141px; top: 1145px; font-size: 11px; color: var(--muted); white-space: nowrap; }
  .footer .brand {
    position: absolute; left: 276px; top: 1128px;
    font-family: "Open Sans", Arial, sans-serif;
    font-weight: 600; font-size: 26px; line-height: 34px; color: var(--ink);
  }
  .footer .rights { position: absolute; left: 276px; top: 1166px; font-size: 8px; color: var(--muted); white-space: nowrap; }
</style>
</head>
<body>
<div class="sheet">
  <div class="hero-visual" role="img" aria-label="Dark photo of a glowing grey globe with connection lines across the continents"></div>

  <section class="offer-panel">
    <svg class="panel-shape" width="348" height="353" viewBox="0 0 348 353" aria-hidden="true">
      <polygon points="0,0 348,0 348,302 222,302 174,353 126,302 0,302" fill="var(--accent)"/>
    </svg>
    <h1 class="offer-title">PAY-PER-USE<br>LOCATION</h1>
    <div class="offer-icons" aria-hidden="true">
      <svg viewBox="0 0 44 44"><circle cx="22" cy="22" r="21" fill="var(--accent-dark)" stroke="#fff" stroke-width="1.5"/><path d="M11 31V19l6 4v-4l6 4v-4l6 4V13h4v18z" fill="#fff"/></svg>
      <svg viewBox="0 0 44 44"><circle cx="22" cy="22" r="21" fill="var(--accent-dark)" stroke="#fff" stroke-width="1.5"/><path d="M12 31h20M16 31V20h12v11M19 20v-5h6v5" stroke="#fff" stroke-width="2" fill="none"/></svg>
      <svg viewBox="0 0 44 44"><circle cx="22" cy="22" r="21" fill="var(--accent-dark)" stroke="#fff" stroke-width="1.5"/><path d="M22 12a7 7 0 0 1 7 7c0 5-7 13-7 13s-7-8-7-13a7 7 0 0 1 7-7z" fill="#fff"/><circle cx="22" cy="19" r="2.5" fill="var(--accent-dark)"/></svg>
    </div>
    <h2 class="offer-reach">ANYWHERE<br>IN THE WORLD AS<br>MUTUALLY AGREED</h2>
    <p class="offer-note">(Immediate Sites Available in<br>Singapore and Indonesia)</p>
  </section>

  <div class="broker-note">Serious Enquiries<br>of Brokers &amp; Agents<br>are Welcome</div>

  <section class="details">
    <p class="strong">What will be the Estimates Cost?</p>
    <p class="strong">Depends on Feasibilities and as Mutually Agreed</p>
    <div class="divider"></div>
    <p class="strong">Our Existing Customers include Food &amp; Life Science Enterprises</p>
    <div class="divider"></div>
    <p>Contact us at : PayPerUse@Lumora.com.sg</p>
    <p class="strong">and you may be surprised with our solutions &amp; possibilities</p>
    <p class="highlight">A great opportunity not to be missed!</p>
  </section>

  <footer class="footer">
    <span class="contract">Subject to Contract with</span>
    <span class="brand">Lumora</span>
    <span class="rights">All Rights Reserved. Copyright © 1 June 2020</span>
  </footer>
</div>
</body>
</html>
```